BrimFalcon Business Cards

We have a defined brand. Please visit our website to get a feel for the product and the color pallets. www.brimfalcon-example.com

We need an updated, world class business card design. (See the attached existing card design). Please utilize BOTH sides of the card as shown and be creative with the layout. I do want the horse head icon to be positioned as it is with the existing card.

The remainder of the layout can be customized and I also want it vertically oriented.

Attached are the logo files and please use the colors as follows:
Green - #A5CE39
Tan - #CDBD99
Black

Feel free to play with the colors.

```html
<!DOCTYPE html>
<html lang="en">
<head>
<meta charset="utf-8">
<title>BrimFalcon Labs — Business Card</title>
<link rel="stylesheet" href="https://fonts.googleapis.com/css2?family=Montserrat:wght@400;500;700&display=swap">
<style>
  :root {
    --backdrop: #3a3a3c;
    --card-dark: #242424;
    --brand-green: #a5ce39;
    --band-deep: #13801f;
    --band-bright: #c4d92c;
    --ink: #111111;
    --paper: #f2f2f2;
  }
  * { margin: 0; padding: 0; box-sizing: border-box; }
  html, body { width: 1200px; height: 1108px; overflow: hidden; }
  body {
    background: var(--backdrop);
    font-family: "Montserrat", sans-serif;
    position: relative;
  }
  .card {
    position: absolute;
    width: 420px;
    height: 680px;
    border-radius: 26px;
    overflow: hidden;
    box-shadow: 0 18px 40px rgba(0,0,0,0.45);
  }
  .card--front { left: 150px; top: 214px; background: var(--card-dark); }
  .card--back { left: 630px; top: 214px; background: var(--brand-green); }

  .brand {
    display: flex;
    align-items: center;
    justify-content: center;
    gap: 10px;
    font-weight: 700;
    letter-spacing: 0.5px;
  }
  .brand__dot { width: 26px; height: 26px; border-radius: 50%; }
  .brand__name { font-size: 34px; }
  .brand__labs { font-size: 12px; align-self: flex-end; margin-bottom: 6px; margin-left: -4px; }

  .card--front .brand { margin-top: 100px; color: var(--paper); }
  .card--front .brand__dot { background: var(--paper); }

  .name-band {
    margin-top: 70px;
    height: 120px;
    background: linear-gradient(90deg, var(--band-deep) 0%, var(--band-bright) 50%, var(--band-deep) 100%);
    display: flex;
    flex-direction: column;
    align-items: center;
    justify-content: center;
    color: var(--ink);
  }
  .name-band__name { font-size: 32px; font-weight: 700; letter-spacing: 1.5px; text-transform: uppercase; }
  .name-band__title { font-size: 17px; font-weight: 500; margin-top: 2px; }

  .contact {
    margin-top: 56px;
    text-align: center;
    color: var(--paper);
    font-size: 19px;
    line-height: 1.3;
  }
  .contact__lines + .contact__lines { margin-top: 18px; }

  .card--back .brand { margin-top: 82px; color: var(--ink); }
  .card--back .brand__name { font-size: 40px; }

  .emblem-area {
    position: absolute;
    left: 0;
    bottom: 0;
    width: 420px;
    height: 430px;
    background: radial-gradient(ellipse at 55% 55%, #0b0b0b 0%, #0b0b0b 45%, #2f3c12 80%, var(--brand-green) 100%);
  }
</style>
</head>
<body>
  <section class="card card--front">
    <div class="brand">
      <span class="brand__dot"></span>
      <span class="brand__name">BrimFalcon</span>
      <span class="brand__labs">LABS</span>
    </div>
    <div class="name-band">
      <span class="name-band__name">Dana Mercer</span>
      <span class="name-band__title">President &amp; CEO</span>
    </div>
    <div class="contact">
      <p class="contact__lines">BrimFalcon Labs LLC<br>Northvale, Prairieland<br>Canada</p>
      <p class="contact__lines">P. 555.010.2650<br>dana@brimfalcon-example.com<br>brimfalconlabs-example.com</p>
    </div>
  </section>

  <section class="card card--back">
    <div class="brand">
      <span class="brand__name">BrimFalcon</span>
      <span class="brand__labs">LABS</span>
    </div>
    <div class="emblem-area" role="img" aria-label="Large black brand emblem illustration on green, anchored to the lower left of the card"></div>
  </section>
</body>
</html>
```